brovane business card

We are a commercial cleaning/janitorial service company our main target is building owners and managers.
Would like to see the icon as a background shadow in the front and the full logo in white on the back with a blue background.  On the card:
Dorn Hassel, Operations Manager, dorn@brovane-mail.com
48371-B Orchard Ln. 9 #402
Maplewood, OH 58217
555.304.8812, 800.555.4170

Updates
please include cell 555.618.2243
                                   
Thank you
If possible the fading logo on the front should be very subtle and light and lets look at centering that as well
thanks

Industry/Entity Type
Building
Look and feel
Each slider illustrates characteristics of the customer's brand and the style your logo design should communicate.

```html
<!DOCTYPE html>
<html lang="en">
<head>
<meta charset="utf-8">
<title>brovane business card</title>
<link rel="stylesheet" href="https://fonts.googleapis.com/css2?family=Arimo:wght@400;700&display=swap">
<style>
  :root {
    --page: #e9eaec;
    --blue: #1f7fc0;
    --blue-deep: #0f5f99;
    --blue-light: #3ea2dc;
    --ink: #2b2b2b;
    --grey-swoosh: #3a3d42;
    --white: #ffffff;
  }
  * { margin: 0; padding: 0; box-sizing: border-box; }
  html, body {
    width: 1200px; height: 901px; overflow: hidden;
    background: var(--page);
    font-family: "Arimo", Arial, sans-serif;
  }
  .stage {
    width: 1200px; height: 901px;
    display: flex; flex-direction: column; align-items: center; justify-content: center;
    gap: 56px;
  }
  .card {
    position: relative;
    width: 580px; height: 330px;
    border-radius: 22px;
    overflow: hidden;
    box-shadow: 0 6px 18px rgba(0,0,0,0.18);
  }

  /* Back */
  .card-back {
    background: radial-gradient(ellipse at 40% 45%, var(--blue-light) 0%, var(--blue) 45%, var(--blue-deep) 100%);
    color: var(--white);
  }
  .back-brand {
    position: absolute; left: 0; right: 0; top: 118px;
    display: flex; align-items: center; justify-content: center; gap: 18px;
  }
  .brand-dot {
    width: 70px; height: 70px; border-radius: 50%;
    background: var(--white);
  }
  .back-brand .brand-name {
    font-size: 62px; font-weight: 700; letter-spacing: -1px; color: var(--white);
  }
  .back-web {
    position: absolute; right: 34px; bottom: 24px;
    font-size: 14px; color: var(--white);
  }

  /* Front */
  .card-front { background: var(--white); }
  .front-band { position: absolute; left: 0; top: 0; width: 580px; height: 130px; }
  .contact {
    position: absolute; left: 34px; top: 150px;
    color: var(--ink); font-size: 16px; line-height: 1.2;
  }
  .address { color: var(--blue); font-size: 15px; margin-bottom: 8px; }
  .contact-list { list-style: none; }
  .contact-list li { display: flex; align-items: center; gap: 10px; margin-bottom: 5px; }
  .contact-icon { width: 16px; height: 16px; flex: none; }
  .front-brand {
    position: absolute; right: 40px; top: 150px;
    width: 230px; display: flex; flex-direction: column; align-items: center;
  }
  .front-brand .brand-line { display: flex; align-items: center; gap: 12px; }
  .front-brand .brand-dot { width: 40px; height: 40px; background: var(--blue); }
  .front-brand .brand-name { font-size: 40px; font-weight: 700; color: var(--blue); letter-spacing: -0.5px; }
  .person { margin-top: 24px; text-align: center; }
  .person-name {
    font-size: 17px; font-weight: 700; color: var(--ink);
    font-variant: small-caps; letter-spacing: 0.5px;
  }
  .person-title { font-size: 14px; color: var(--blue); margin-top: 3px; }
</style>
</head>
<body>
<main class="stage">

  <section class="card card-back">
    <div class="back-brand">
      <span class="brand-dot"></span>
      <span class="brand-name">brovane</span>
    </div>
    <p class="back-web">www.brovane-clean.com</p>
  </section>

  <section class="card card-front">
    <svg class="front-band" viewBox="0 0 580 130" preserveAspectRatio="none" aria-hidden="true">
      <defs>
        <linearGradient id="bandFill" x1="0" y1="0" x2="0" y2="1">
          <stop offset="0" stop-color="#0f6eaf"/>
          <stop offset="1" stop-color="#3aa0db"/>
        </linearGradient>
      </defs>
      <path d="M0 0 H580 V92 C500 70 420 58 300 58 C190 58 90 64 0 72 Z" fill="url(#bandFill)"/>
      <path d="M130 60 C260 50 420 58 580 100 V112 C430 72 290 60 130 60 Z" fill="var(--grey-swoosh)"/>
    </svg>

    <div class="contact">
      <p class="address">48371-B Orchard Ln. 9 #402<br>Maplewood, OH 58217</p>
      <ul class="contact-list">
        <li>
          <svg class="contact-icon" viewBox="0 0 16 16" aria-hidden="true"><circle cx="8" cy="8" r="8" fill="var(--blue)"/><path d="M4 6.5c0-1 1.5-2 4-2s4 1 4 2l-1.5.6-.5-1.1h-4l-.5 1.1zM5 8h6l.6 3.5H4.4z" fill="#fff"/></svg>
          555.304.8812, 800.555.4170
        </li>
        <li>
          <svg class="contact-icon" viewBox="0 0 16 16" aria-hidden="true"><circle cx="8" cy="8" r="8" fill="var(--blue)"/><rect x="5.5" y="3.5" width="5" height="9" rx="1" fill="#fff"/><rect x="6.3" y="4.6" width="3.4" height="5" fill="var(--blue)"/></svg>
          555.618.2243
        </li>
        <li>
          <svg class="contact-icon" viewBox="0 0 16 16" aria-hidden="true"><circle cx="8" cy="8" r="8" fill="var(--blue)"/><rect x="4" y="5" width="8" height="6" fill="#fff"/><path d="M4 5l4 3.3L12 5" fill="none" stroke="var(--blue)" stroke-width="0.9"/></svg>
          dorn@brovane-mail.com
        </li>
        <li>
          <svg class="contact-icon" viewBox="0 0 16 16" aria-hidden="true"><circle cx="8" cy="8" r="8" fill="var(--blue)"/><circle cx="8" cy="8" r="4.5" fill="none" stroke="#fff" stroke-width="1"/><path d="M3.5 8h9M8 3.5c-2 2.5-2 6.5 0 9M8 3.5c2 2.5 2 6.5 0 9" fill="none" stroke="#fff" stroke-width="0.8"/></svg>
          www.brovane-clean.com
        </li>
      </ul>
    </div>

    <div class="front-brand">
      <div class="brand-line">
        <span class="brand-dot"></span>
        <span class="brand-name">brovane</span>
      </div>
      <div class="person">
        <p class="person-name">Dorn Hassel</p>
        <p class="person-title">Operations Manager</p>
      </div>
    </div>
  </section>

</main>
</body>
</html>
```